Walk Beside The River

Business Card design

Target Market(s)

People who require support in the commnity

Industry/Entity Type

Mental Health Support

Contact Information for Business Card

Mental Health Support Rosalind Tavener walkbesidetheriver@mailcove.com.au 0481 637 092 PO Box 926 Wattlebrook QLD 4593

Colors
6B429C
8869AF
B7A5CE
E3DAEB
F3F0F8

Requirements
Must have
• Logo & details listed above
Should not have
• No red or orange

```html
<!DOCTYPE html>
<html lang="en">
<head>
<meta charset="utf-8">
<title>Walk Beside The River — Business Card</title>
<link rel="stylesheet" href="https://fonts.googleapis.com/css2?family=Montserrat:wght@500;600;800&display=swap">
<style>
  :root {
    --violet: #6B429C;
    --violet-mid: #8869AF;
    --violet-soft: #B7A5CE;
    --lilac: #E3DAEB;
    --mist: #F3F0F8;
    --violet-deep: #3B2470;
    --white: #FFFFFF;
  }
  * { box-sizing: border-box; margin: 0; padding: 0; }
  html, body {
    width: 1200px;
    height: 1000px;
    overflow: hidden;
    background: var(--mist);
    font-family: "Montserrat", Arial, sans-serif;
  }
  .sheet {
    position: relative;
    width: 1200px;
    height: 1000px;
  }
  .card {
    position: absolute;
    left: 300px;
    width: 600px;
    height: 343px;
    border-radius: 4px;
    box-shadow: 0 10px 28px rgba(59, 36, 112, 0.18);
    overflow: hidden;
  }

  /* Front */
  .card--front {
    top: 118px;
    background: var(--white);
  }
  .brand {
    position: absolute;
    left: 30px;
    top: 0;
    width: 190px;
    height: 343px;
    display: flex;
    flex-direction: column;
    align-items: center;
    justify-content: center;
    gap: 14px;
  }
  .brand__dot {
    width: 118px;
    height: 118px;
    border-radius: 50%;
    background: linear-gradient(160deg, var(--violet-mid), var(--violet));
  }
  .brand__name {
    font-weight: 600;
    font-size: 15px;
    letter-spacing: 0.16em;
    text-transform: uppercase;
    color: var(--violet);
    text-align: center;
    line-height: 1.45;
  }
  .divider {
    position: absolute;
    left: 240px;
    top: 52px;
    width: 2px;
    height: 240px;
    background: var(--violet);
  }
  .details {
    position: absolute;
    left: 266px;
    top: 50px;
    right: 20px;
    color: var(--violet);
  }
  .person__name {
    font-weight: 800;
    font-size: 31px;
    letter-spacing: -0.01em;
    color: var(--violet-mid);
    line-height: 1.05;
  }
  .person__role {
    margin-top: 4px;
    margin-left: 120px;
    font-weight: 500;
    font-size: 8px;
    letter-spacing: 0.22em;
    color: var(--violet-mid);
  }
  .contact {
    list-style: none;
    margin-top: 26px;
    display: flex;
    flex-direction: column;
    gap: 15px;
  }
  .contact__item {
    display: flex;
    align-items: center;
    gap: 12px;
    font-weight: 500;
    font-size: 13.5px;
    line-height: 1.2;
  }
  .contact__icon {
    flex: none;
    width: 16px;
    height: 16px;
    fill: var(--violet);
  }

  /* Back */
  .card--back {
    top: 540px;
    background: linear-gradient(200deg, var(--violet-soft) 0%, var(--violet-mid) 35%, var(--violet) 65%, var(--violet-deep) 100%);
    display: flex;
    flex-direction: column;
    align-items: center;
    justify-content: center;
    gap: 16px;
  }
  .back__ring {
    width: 150px;
    height: 150px;
    border-radius: 50%;
    border: 3px solid var(--white);
  }
  .back__name {
    font-weight: 600;
    font-size: 15px;
    letter-spacing: 0.2em;
    text-transform: uppercase;
    color: var(--white);
  }
</style>
</head>
<body>
<main class="sheet">

  <section class="card card--front" aria-label="Business card front">
    <div class="brand">
      <span class="brand__dot" aria-hidden="true"></span>
      <p class="brand__name">Walk Beside<br>The River</p>
    </div>

    <span class="divider" aria-hidden="true"></span>

    <div class="details">
      <h1 class="person__name">Rosalind Tavener</h1>
      <p class="person__role">MENTAL HEALTH SUPPORT</p>

      <ul class="contact">
        <li class="contact__item">
          <svg class="contact__icon" viewBox="0 0 16 16" aria-hidden="true"><path d="M8 0.5a5.5 5.5 0 0 0-5.5 5.5c0 4.2 5.5 9.5 5.5 9.5s5.5-5.3 5.5-9.5A5.5 5.5 0 0 0 8 0.5zm0 7.6a2.1 2.1 0 1 1 0-4.2 2.1 2.1 0 0 1 0 4.2z"/></svg>
          <span>PO Box 926 Wattlebrook<br>QLD 4593</span>
        </li>
        <li class="contact__item">
          <svg class="contact__icon" viewBox="0 0 16 16" aria-hidden="true"><path d="M4.2 1.2l2.1 3.2-1.5 1.4c.8 2 2.3 3.6 4.3 4.5l1.4-1.5 3.2 2.1-1 2.6c-.3.6-.9.9-1.5.8C6.2 13.6 2.4 9.8 1.7 4.9c-.1-.6.2-1.2.8-1.5z"/></svg>
          <span>0481 637 092</span>
        </li>
        <li class="contact__item">
          <svg class="contact__icon" viewBox="0 0 16 16" aria-hidden="true"><path d="M1 3.5h14v1.2L8 9 1 4.7zM1 6.3l7 4.3 7-4.3v6.2H1z"/></svg>
          <span>walkbesidetheriver@mailcove.com.au</span>
        </li>
        <li class="contact__item">
          <svg class="contact__icon" viewBox="0 0 16 16" aria-hidden="true"><path d="M8 1a7 7 0 1 0 0 14A7 7 0 0 0 8 1zm4.9 6.3h-2.1a11 11 0 0 0-.9-4.3 5.6 5.6 0 0 1 3 4.3zM8 2.5c.6.8 1.2 2.5 1.3 4.8H6.7C6.8 5 7.4 3.3 8 2.5zM6.1 3a11 11 0 0 0-.9 4.3H3.1A5.6 5.6 0 0 1 6.1 3zM3.1 8.7h2.1c.1 1.7.4 3.2.9 4.3a5.6 5.6 0 0 1-3-4.3zM8 13.5c-.6-.8-1.2-2.5-1.3-4.8h2.6c-.1 2.3-.7 4-1.3 4.8zm1.9-.5c.5-1.1.8-2.6.9-4.3h2.1a5.6 5.6 0 0 1-3 4.3z"/></svg>
          <span>walkbesidetheriver@mailcove.com.au</span>
        </li>
      </ul>
    </div>
  </section>

  <section class="card card--back" aria-label="Business card back">
    <span class="back__ring" aria-hidden="true"></span>
    <p class="back__name">Walk Beside The River</p>
  </section>

</main>
</body>
</html>
```